Real Estate Business Card

On the front side I want to have my info, my brokerage info.
On the back side I want have my complany’s logo, website and Facebook link. I will provide all this once I select a design.

I would like to see Black background and gold text, Dark Blue and gold text and White and blue text designs

Font styles to use
Sans Serif
Script

```html
<!DOCTYPE html>
<html lang="en">
<head>
<meta charset="utf-8">
<title>Stonegate Real Estate – Business Card</title>
<link rel="stylesheet" href="https://fonts.googleapis.com/css2?family=Montserrat:wght@800&family=Roboto:wght@400;500;700&display=swap">
<style>
  :root {
    --canvas: #202022;
    --card: #1b1b1d;
    --red: #d8343a;
    --red-light: #ee4a4f;
    --gold: #ecd27a;
    --white: #ffffff;
    --steel: #8a93a6;
  }
  * { margin: 0; padding: 0; box-sizing: border-box; }
  html, body { width: 1200px; height: 900px; overflow: hidden; }
  body {
    background: var(--canvas);
    font-family: "Roboto", Arial, sans-serif;
    position: relative;
  }
  .card {
    position: absolute;
    left: 240px;
    width: 720px;
    height: 400px;
    background: var(--card);
    overflow: hidden;
    box-shadow: 0 10px 30px rgba(0,0,0,.5);
  }
  .card--back { top: 35px; }
  .card--front { top: 465px; }

  /* back side */
  .brand-block {
    position: absolute;
    left: 60px;
    top: 40px;
    width: 250px;
    height: 250px;
    background: var(--red);
  }
  .brand-name {
    font-family: "Montserrat", Arial, sans-serif;
    font-weight: 800;
    color: var(--steel);
    text-transform: uppercase;
    line-height: 1;
  }
  .card--back .brand-name {
    position: absolute;
    right: 40px;
    bottom: 48px;
    font-size: 34px;
    text-align: right;
  }
  .brand-name small {
    display: block;
    font-size: .42em;
    letter-spacing: .5em;
    margin-top: 6px;
  }

  /* front side */
  .brand-lockup {
    position: absolute;
    left: 50px;
    top: 85px;
    display: flex;
    align-items: center;
    gap: 14px;
  }
  .brand-lockup__square {
    width: 46px;
    height: 46px;
    background: var(--red);
    flex: none;
  }
  .card--front .brand-name { font-size: 30px; }

  .contact {
    position: absolute;
    left: 400px;
    top: 50px;
    color: var(--white);
    font-size: 17px;
    line-height: 1.4;
  }
  .contact__name {
    font-weight: 700;
    font-size: 26px;
    color: var(--gold);
    line-height: 1.1;
  }
  .contact__title {
    font-weight: 500;
    font-size: 17px;
    color: var(--red);
    margin-bottom: 10px;
  }
  .contact__address { margin-bottom: 8px; }
  .contact__label { color: var(--gold); font-weight: 500; margin-right: 6px; }

  .web-band {
    position: absolute;
    left: 0;
    right: 0;
    bottom: 40px;
    height: 58px;
    background: linear-gradient(90deg, var(--red), var(--red-light));
    display: flex;
    align-items: center;
    padding-left: 130px;
  }
  .web-band__url {
    color: var(--white);
    font-size: 18px;
    letter-spacing: .45em;
    font-weight: 500;
  }
  .web-band__square {
    position: absolute;
    right: 50px;
    bottom: 0;
    width: 58px;
    height: 58px;
    background: var(--card);
    border: 6px solid var(--red);
  }
</style>
</head>
<body>
  <section class="card card--back" aria-label="Card back">
    <div class="brand-block"></div>
    <div class="brand-name">Stonegate<small>Real Estate</small></div>
  </section>

  <section class="card card--front" aria-label="Card front">
    <div class="brand-lockup">
      <div class="brand-lockup__square"></div>
      <div class="brand-name">Stonegate<small>Real Estate</small></div>
    </div>

    <div class="contact">
      <p class="contact__name">DANIEL REYES</p>
      <p class="contact__title">CEO/FOUNDER</p>
      <p class="contact__address">4120 Willow Creek Road<br>Juneau, Alaska 99801</p>
      <p><span class="contact__label">P:</span>907 555 0142</p>
      <p><span class="contact__label">M:</span>907 555 0187</p>
      <p><span class="contact__label">E:</span>daniel@stonegatehomes.com</p>
      <p><span class="contact__label">FB:</span>/stonegatehomes</p>
    </div>

    <div class="web-band">
      <span class="web-band__url">www.stonegatehomes.com</span>
      <div class="web-band__square"></div>
    </div>
  </section>
</body>
</html>
```